Brand and Marketing Coach Needs PDF Designed

I have content that i need placed into a simple but great PDF design. The PDF is about the formula I use to build personal brands. This is geared towards entrepreneurs, experts, coaches, therapists, wellness practitioners, and indpendent business owners who serve to improve the lives of others.
The company name is changing from TorvelCast to Selling with the Village (I don't have that logo yet, so working backwards a bit. For now, the TorvelCast logo can be used.) My brand is NOT formal and corporate, but it's also not neon-pink and screaming at you. It's down to earth, hip, a bit modern but warm. It's about no BS and authenticity. The final deliverable should make the reader feel focused, smart, motivated and hopeful.

Target Market(s)

Conscious entrepreneurs and small business owners. this one is specifically for pharmacy entrepreneurs but this will be used for various audiences later.

Font styles to use
Sans Serif

Colors
eaf1f7
3377b5
6b449b
f37122
faa54b
f68e4e
ffc214

Requirements
Must have
• Modern design. colors that match logo - 4e5583 (i think that is the blue.) d65a40.
• Could have these colors as well: c6a254, 01bcc3
• But open to other colors
Nice to have
• I'd like to see some ways to make this PDF simple and readable, and eye-catching. I'd also like to use the uploaded ebooks for design ideas.
Should not have
• neon colors, clip art

```html
<!DOCTYPE html>
<html lang="en">
<head>
<meta charset="utf-8">
<title>Follow the Personal Brand Formula</title>
<link rel="stylesheet" href="https://fonts.googleapis.com/css2?family=Playfair+Display:wght@400&family=EB+Garamond:wght@400;600&family=Archivo:ital,wght@1,800&display=swap">
<style>
  :root {
    --canvas: #ffffff;
    --note-red: #ff0000;
    --indigo: #4f5785;
    --ink: #1a1a1a;
    --orange: #f37122;
    --orange-soft: #f68e4e;
    --frame: #222222;
    --paper: #ffffff;
  }
  * { margin: 0; padding: 0; box-sizing: border-box; }
  html, body {
    width: 1200px;
    height: 546px;
    overflow: hidden;
    background: var(--canvas);
  }
  .canvas {
    position: relative;
    width: 1200px;
    height: 546px;
  }
  .review-note {
    position: absolute;
    top: 24px;
    left: 0;
    width: 100%;
    text-align: center;
    font-family: "Archivo", Arial, sans-serif;
    font-style: italic;
    font-weight: 800;
    font-size: 25px;
    letter-spacing: 0.2px;
    color: var(--note-red);
  }
  .section-cover {
    position: absolute;
    left: 33px;
    top: 86px;
    width: 558px;
    height: 430px;
    background: var(--indigo);
    color: #fff;
    font-family: "Playfair Display", Georgia, serif;
    text-align: center;
  }
  .section-number {
    position: absolute;
    top: 84px;
    width: 100%;
    font-size: 132px;
    line-height: 1;
  }
  .section-title {
    position: absolute;
    top: 226px;
    width: 100%;
    font-size: 52px;
    line-height: 63px;
    font-weight: 400;
    text-transform: uppercase;
  }
  .page {
    position: absolute;
    left: 610px;
    top: 86px;
    width: 561px;
    height: 431px;
    background: var(--paper);
    border: 1px solid var(--frame);
    font-family: "EB Garamond", Garamond, serif;
    color: var(--ink);
  }
  .step {
    position: absolute;
    left: 53px;
    width: 460px;
  }
  .step--motivators { top: 45px; }
  .step--value { top: 195px; }
  .step-header {
    display: flex;
    align-items: center;
    height: 34px;
    margin-left: -2px;
  }
  .step-badge {
    width: 34px;
    height: 34px;
    flex: none;
  }
  .step-badge text {
    font-family: "Playfair Display", Georgia, serif;
    font-style: italic;
    font-size: 22px;
    fill: #fff;
  }
  .step-name {
    margin-left: 12px;
    font-family: "EB Garamond", Garamond, serif;
    font-size: 21px;
    color: var(--orange-soft);
    letter-spacing: 0.3px;
  }
  .step-lead {
    margin-top: 19px;
    font-size: 13.6px;
    font-weight: 600;
    line-height: 14px;
  }
  .step-body {
    margin-top: 1px;
    font-size: 10.5px;
    line-height: 11.7px;
    width: 455px;
  }
  .page-number {
    position: absolute;
    top: 391px;
    left: 0;
    width: 100%;
    padding-left: 46px;
    text-align: center;
    font-size: 7px;
    font-variant: small-caps;
    text-transform: none;
    letter-spacing: 0.3px;
  }
</style>
</head>
<body>
<div class="canvas">
  <p class="review-note">PLS. CONFIRM IF THIS ON THE RIGHT TRACK. THANKS!</p>

  <section class="section-cover">
    <div class="section-number">3</div>
    <h1 class="section-title">Follow the<br>Personal<br>Brand Formula</h1>
  </section>

  <section class="page">
    <article class="step step--motivators">
      <div class="step-header">
        <svg class="step-badge" viewBox="0 0 34 34" aria-hidden="true">
          <circle cx="17" cy="17" r="17" fill="var(--orange-soft)"/>
          <text x="17" y="25" text-anchor="middle">1</text>
        </svg>
        <h2 class="step-name">MOTIVATORS</h2>
      </div>
      <p class="step-lead">Your WHY and the real reason you created this business.</p>
      <p class="step-body">This is what motivates you to serve people as you do, and the purpose behind your business. Because your personal brand must reflect your purpose and values, your mission, tagline, and messaging won’t align with you or communicate your real value. When this happens, you attract the wrong clients or none at all. When your purpose is driving your business, it flows much easier, and you are happy doing LIFE!</p>
    </article>

    <article class="step step--value">
      <div class="step-header">
        <svg class="step-badge" viewBox="0 0 34 34" aria-hidden="true">
          <circle cx="17" cy="17" r="17" fill="var(--orange-soft)"/>
          <text x="17" y="25" text-anchor="middle">2</text>
        </svg>
        <h2 class="step-name">VALUE</h2>
      </div>
      <p class="step-lead">Your expertise and the results your clients get from working with you.</p>
      <p class="step-body">Your prospects must understand what you do and what you’re asking them to do. As time and attention span continue to decrease, people just won’t stick around long enough to research how you can help them. To succinctly communicate your value, you must know simplify who you are, what you do, and how you do it into a clear value statement. Getting this right means you also have a great bit of content already written for your website.</p>
    </article>

    <p class="page-number">Page x of xx</p>
  </section>
</div>
</body>
</html>
```